Northglint Name Card & Logo Design

We need a new business card design and a logo for our company as well. Our company is in the computer retail business. We provide our walk in customers with a wide range of computer products from mouse to complete desktop.Anything you need in a computer? We got it. Our area of aim is to provide customers with value and trust in our service & products .We provide customization of Computer desktop/ Repairs of laptop/desktop.
You may want to take a look at our Website for more information.
www.northglint-demo.com.sg
Industry/Entity Type
Computer
Contact Information for Business Card
Northglint Technology
Tan Wei Lun
Operations Manager
+65 6000 1472
+65 9000 3825
tanwl@northglint-demo.com.sg
Corporate Sales Enquries : corporatesales@northglint-demo.com.sg

```html
<!DOCTYPE html>
<html lang="en">
<head>
<meta charset="utf-8">
<title>Northglint Technology – Business Card</title>
<link rel="stylesheet" href="https://fonts.googleapis.com/css2?family=Saira:wght@400;500&display=swap">
<style>
  :root {
    --backdrop: #2b2b2d;
    --card-light: #ffffff;
    --card-shade: #dcdcdc;
    --brand-orange: #f07f22;
    --ink-dark: #3f3f42;
    --ink-mid: #55565a;
  }
  * { box-sizing: border-box; margin: 0; padding: 0; }
  html, body { width: 1200px; height: 755px; overflow: hidden; }
  body {
    background: var(--backdrop);
    font-family: "Saira", "Arial", sans-serif;
    position: relative;
  }
  .card {
    position: absolute;
    top: 212px;
    width: 540px;
    height: 330px;
    background: radial-gradient(ellipse at 55% 45%, var(--card-light) 0%, #f3f3f3 50%, var(--card-shade) 100%);
    box-shadow: 0 10px 30px rgba(0,0,0,0.5);
  }
  .card--front { left: 45px; }
  .card--back { left: 615px; }

  .holder { position: absolute; left: 210px; top: 46px; }
  .holder__name {
    color: var(--brand-orange);
    font-size: 20px;
    font-weight: 500;
    letter-spacing: 0.04em;
    line-height: 1.1;
  }
  .holder__title {
    color: var(--ink-mid);
    font-size: 11px;
    letter-spacing: 0.08em;
  }
  .contact-list { position: absolute; left: 222px; top: 112px; list-style: none; }
  .contact-list li,
  .enquiry {
    display: flex;
    align-items: center;
    gap: 8px;
    color: var(--ink-dark);
    font-size: 13px;
    letter-spacing: 0.03em;
    height: 22px;
    white-space: nowrap;
  }
  .icon {
    width: 15px; height: 15px;
    border-radius: 50%;
    background: var(--brand-orange);
    display: flex; align-items: center; justify-content: center;
    flex: none;
  }
  .icon svg { width: 9px; height: 9px; }
  .divider {
    position: absolute;
    left: 238px; top: 214px;
    width: 272px; height: 1px;
    background: var(--brand-orange);
  }
  .enquiry { position: absolute; left: 238px; top: 224px; font-size: 12px; letter-spacing: 0.02em; }

  .brand { display: flex; flex-direction: column; align-items: center; gap: 10px; }
  .brand__dot {
    width: 42px; height: 42px; border-radius: 50%;
    background: var(--brand-orange);
  }
  .brand__name {
    color: var(--brand-orange);
    font-size: 17px;
    font-weight: 400;
    letter-spacing: 0.05em;
    white-space: nowrap;
  }
  .card--front .brand { position: absolute; left: 28px; bottom: 22px; }
  .card--back .brand { position: absolute; left: 50%; top: 50%; transform: translate(-50%, -50%); }
  .card--back .brand__dot { width: 54px; height: 54px; }
  .card--back .brand__name { font-size: 20px; }
</style>
</head>
<body>
  <section class="card card--front">
    <div class="holder">
      <h1 class="holder__name">TAN WEI LUN</h1>
      <p class="holder__title">OPERATIONS MANAGER</p>
    </div>

    <ul class="contact-list">
      <li>
        <span class="icon"><svg viewBox="0 0 10 10"><path d="M2 1 L4 1 L4.6 3 L3.6 3.8 Q4.6 5.6 6.2 6.4 L7 5.4 L9 6 L9 8 Q5 9 2 5.5 Q1 3 2 1 Z" fill="#fff"/></svg></span>
        +65 6000 1472 / +65 9000 3825
      </li>
      <li>
        <span class="icon"><svg viewBox="0 0 10 10"><rect x="1" y="2.5" width="8" height="5.5" fill="#fff"/><path d="M1 2.5 L5 5.8 L9 2.5" stroke="#f07f22" stroke-width="0.9" fill="none"/></svg></span>
        tanwl@northglint-demo.com.sg
      </li>
      <li>
        <span class="icon"><svg viewBox="0 0 10 10" fill="none" stroke="#fff" stroke-width="0.9"><circle cx="5" cy="5" r="4"/><ellipse cx="5" cy="5" rx="1.8" ry="4"/><path d="M1 5 H9"/></svg></span>
        www.northglint-demo.com.sg
      </li>
    </ul>

    <div class="divider"></div>
    <p class="enquiry">
      <span class="icon"><svg viewBox="0 0 10 10"><rect x="1" y="2.5" width="8" height="5.5" fill="#fff"/><path d="M1 2.5 L5 5.8 L9 2.5" stroke="#f07f22" stroke-width="0.9" fill="none"/></svg></span>
      corporatesales@northglint-demo.com.sg
    </p>

    <div class="brand">
      <span class="brand__dot"></span>
      <span class="brand__name">Northglint Technology</span>
    </div>
  </section>

  <section class="card card--back">
    <div class="brand">
      <span class="brand__dot"></span>
      <span class="brand__name">Northglint Technology</span>
    </div>
  </section>
</body>
</html>
```